Awesome photographers card for an awesome new business

Double sided business card Black background and silver logo in middle on one side. Details on otherside. please keep it simple

Industry/Entity Type

Photographer

Contact Information for Business Card

Gerald Fenwick
0452817360
GeraldFenwickPhotography47@mailbox.test
www.GeraldFenwickPhotography.test.au
Instagram _Gerald_fenwick

Requirements
Must have
• My logo in Silver
• please use instagram logo instead of "Instagram"

```html
<!DOCTYPE html>
<html lang="en">
<head>
<meta charset="utf-8">
<title>Gerald Fenwick Photography – Business Card</title>
<link href="https://fonts.googleapis.com/css2?family=Roboto:wght@400;500&family=Roboto+Condensed:wght@500&display=swap" rel="stylesheet">
<style>
  :root {
    --stage: #262626;
    --ink: #161616;
    --silver-light: #d2d2d2;
    --silver-mid: #a9a9a9;
    --silver-dark: #7d7d7d;
    --white: #ffffff;
    --mark-front: #cfcfcf;
    --mark-back: #2f2f2f;
  }
  * { margin: 0; padding: 0; box-sizing: border-box; }
  html, body {
    width: 1200px; height: 960px; overflow: hidden;
    background: var(--stage);
  }
  .canvas { position: relative; width: 1200px; height: 960px; }
  .card {
    position: absolute; width: 598px; height: 342px; overflow: hidden;
    box-shadow: 0 4px 10px rgba(0,0,0,.55);
  }
  .card--front {
    left: 315px; top: 113px;
    background: linear-gradient(100deg, var(--silver-dark) 20%, var(--silver-light) 62%, var(--silver-mid) 100%);
  }
  .card--back {
    left: 312px; top: 472px;
    background: radial-gradient(ellipse at 45% 35%, var(--silver-light) 0%, var(--silver-mid) 55%, var(--silver-dark) 100%);
  }
  .card__art { position: absolute; inset: 0; }
  .brand-mark {
    position: absolute; display: flex; align-items: center; justify-content: center;
    border-radius: 50%;
    font-family: "Roboto", sans-serif; font-weight: 500;
    font-size: 17px; letter-spacing: 1px; text-transform: uppercase;
    text-align: center; line-height: 1.3;
  }
  .card--front .brand-mark {
    left: 75px; top: 42px; width: 166px; height: 166px;
    border: 3px solid var(--mark-front); color: var(--mark-front);
  }
  .card--back .brand-mark {
    left: 210px; top: 82px; width: 176px; height: 176px;
    border: 3px solid var(--mark-back); color: var(--mark-back);
  }
  .contact {
    position: absolute; right: 20px; top: 202px; text-align: right;
    font-family: "Roboto", sans-serif; color: var(--white);
  }
  .contact__name {
    font-family: "Roboto Condensed", sans-serif; font-weight: 500;
    font-size: 21px; margin-bottom: 16px; text-transform: uppercase;
  }
  .contact__list { list-style: none; }
  .contact__item {
    display: flex; justify-content: flex-end; align-items: center;
    font-size: 14px; height: 19px; gap: 7px;
  }
  .contact__icon { width: 14px; height: 14px; flex: none; }
  .back__url {
    position: absolute; left: 0; right: 0; top: 292px; text-align: center;
    font-family: "Roboto", sans-serif; font-size: 14px; letter-spacing: 2.4px;
    color: var(--white);
  }
</style>
</head>
<body>
<main class="canvas">
  <section class="card card--front" aria-label="Business card front">
    <svg class="card__art" viewBox="0 0 598 342" aria-hidden="true">
      <path d="M0 0 H282 C392 8 438 112 332 202 C252 272 110 326 0 342 Z" fill="var(--ink)"/>
      <path d="M300 2 C425 22 448 128 345 212 C262 278 120 330 10 342" fill="none" stroke="var(--ink)" stroke-width="3"/>
    </svg>
    <div class="brand-mark">Gerald<br>Fenwick</div>
    <div class="contact">
      <p class="contact__name">Gerald Fenwick</p>
      <ul class="contact__list">
        <li class="contact__item">0452817360
          <svg class="contact__icon" viewBox="0 0 24 24"><path fill="var(--white)" d="M6.6 10.8a15 15 0 006.6 6.6l2.2-2.2a1 1 0 011-.25 11.4 11.4 0 003.6.57 1 1 0 011 1V20a1 1 0 01-1 1A17 17 0 013 4a1 1 0 011-1h3.5a1 1 0 011 1c0 1.25.2 2.45.57 3.57a1 1 0 01-.25 1z"/></svg>
        </li>
        <li class="contact__item">GeraldFenwickPhotography47@mailbox.test
          <svg class="contact__icon" viewBox="0 0 24 24"><rect x="2" y="5" width="20" height="14" fill="var(--white)"/><path d="M2 5l10 8 10-8" fill="none" stroke="var(--silver-mid)" stroke-width="1.8"/></svg>
        </li>
        <li class="contact__item">www.GeraldFenwickPhotography.test.au
          <svg class="contact__icon" viewBox="0 0 24 24"><circle cx="12" cy="12" r="10" fill="var(--white)"/><path d="M2 12h20M12 2c3 3 3 17 0 20M12 2c-3 3-3 17 0 20" fill="none" stroke="var(--silver-mid)" stroke-width="1.5"/></svg>
        </li>
        <li class="contact__item">Gerald_fenwick
          <svg class="contact__icon" viewBox="0 0 24 24"><rect x="2" y="2" width="20" height="20" rx="3" fill="var(--white)"/></svg>
        </li>
      </ul>
    </div>
  </section>

  <section class="card card--back" aria-label="Business card back">
    <div class="brand-mark">Gerald<br>Fenwick</div>
    <p class="back__url">www.GeraldFenwickPhotography.test.au</p>
  </section>
</main>
</body>
</html>
```